Design a large parking banner – mandatory ticket validation in the shop

Banner Size:
548 cm (width) x 154 cm (height)
Note: The banner will be placed in a metal frame at our parking lot entrance, fully visible to every incoming truck driver. The message must be easy to read from a distance.
Goal of the Banner:
To inform all truck drivers that they must validate their entry ticket inside the shop, even if they are parking for a short time.
The message must be displayed in multiple languages for international drivers.
Mandatory Content:
Main message – in multiple languages (clearly separated or stacked):
Dutch (NL): Vergeet je ticket niet te valideren in de shop – verplicht, ook bij kort parkeren!
French (FR): N'oubliez pas de valider votre ticket à la boutique – obligatoire, même pour un court arrêt !
English (EN): Don't forget to validate your entry ticket in the shop – mandatory, even for short stops!
German (DE): Vergessen Sie nicht, Ihr Einfahrticket im Shop zu entwerten – Pflicht, auch bei kurzem Parken!
Polish (PL): Nie zapomnij zatwierdzić biletu w sklepie – obowiązkowe, nawet przy krótkim postoju!
Romanian (RO): Nu uitați să validați biletul în magazin – obligatoriu, chiar și pentru opriri scurte!
You can include more languages if space allows, but these are essential.
Opening Hours Block (in one section below):
Shop Opening Hours
Mon – Fri: 05:30 – 22:00
Sat & Sun: 08:00 – 22:00
Style & Branding:
The design must match the visual identity of Haulport 41Ter
Please refer to the attached photos of existing parking signage for guidance on colors, typography, and layout style
Our logo (attached) must be clearly visible and professionally integrated
Feel free to use icons or pictograms to visually support the message (e.g., ticket, truck, arrow)
Readability is key – large, bold text and high contrast colors that are visible from a distance
Target Audience:
International truck drivers – people who need fast, clear communication. Not everyone speaks the local language, so visual clarity and multilingual messaging are critical.
File Requirements:
Print-ready file (PDF or EPS) – 300 dpi at 1:10 scale
Include 5 cm bleed on all sides
Provide open source files if possible (AI or PSD)

```html
<!DOCTYPE html>
<html lang="en">
<head>
<meta charset="utf-8">
<title>Haulport 41Ter – Ticket Validation Banner</title>
<link rel="stylesheet" href="https://fonts.googleapis.com/css2?family=Montserrat:wght@300;400;500;600&display=swap">
<style>
  :root {
    --navy: #1c2149;
    --blue: #1a7fc4;
    --red: #d8131c;
    --white: #ffffff;
    --stage: #eef1f5;
    --shop-light: #e9ecef;
    --shop-mid: #b9c2cb;
  }
  * { margin: 0; padding: 0; box-sizing: border-box; }
  html, body {
    width: 1200px; height: 712px; overflow: hidden;
    background: var(--stage);
    font-family: "Montserrat", Arial, sans-serif;
  }
  .banner {
    position: absolute; left: 0; top: 187px;
    width: 1200px; height: 337px;
    overflow: hidden; color: var(--white);
  }
  .banner-bg { position: absolute; inset: 0; }
  .headline-block { position: absolute; left: 40px; top: 22px; width: 500px; }
  .kicker { font-size: 21px; font-weight: 500; letter-spacing: 0.5px; text-transform: uppercase; }
  .headline {
    margin-top: 4px; font-size: 46px; font-weight: 500; line-height: 48px;
    text-transform: uppercase; letter-spacing: 0.3px;
  }
  .mark-blue { background: var(--blue); padding: 0 6px; margin-left: -6px; }
  .mark-red { background: var(--red); padding: 0 5px; }
  .hours { position: absolute; left: 40px; top: 212px; }
  .hours-title { font-size: 22px; font-weight: 600; line-height: 27px; text-transform: uppercase; }
  .hours-list { margin-top: 6px; font-size: 21px; font-weight: 300; line-height: 26px; }
  .notice { position: absolute; left: 568px; top: 34px; width: 345px; }
  .notice-title { font-size: 18px; font-weight: 600; text-transform: uppercase; margin-bottom: 10px; }
  .notice-title .mark-blue { margin-left: 0; padding: 0 5px; }
  .lang-list { list-style: none; }
  .lang-item {
    position: relative; padding-left: 22px; margin-bottom: 7px;
    font-size: 11.5px; font-weight: 300; line-height: 15px;
  }
  .lang-item::before {
    content: "#"; position: absolute; left: 0; top: -2px;
    font-size: 19px; font-weight: 300;
  }
  .brand {
    position: absolute; right: 22px; bottom: 26px;
    font-size: 22px; font-weight: 600; color: var(--navy);
    display: flex; align-items: center; gap: 8px;
  }
  .brand-square { width: 14px; height: 14px; background: var(--navy); }
</style>
</head>
<body>
  <section class="banner">
    <svg class="banner-bg" width="1200" height="337" viewBox="0 0 1200 337">
      <defs>
        <linearGradient id="shopGradient" x1="0" y1="0" x2="1" y2="1">
          <stop offset="0" stop-color="var(--shop-light)"/>
          <stop offset="1" stop-color="var(--shop-mid)"/>
        </linearGradient>
      </defs>
      <rect class="shop-photo" x="860" y="0" width="340" height="337" fill="url(#shopGradient)" role="img" aria-label="Photo of the shop interior with stocked shelves"/>
      <polygon class="navy-panel" points="0,0 880,0 965,200 880,337 0,337" fill="var(--navy)"/>
      <polyline class="red-edge" points="888,0 973,200 888,337" fill="none" stroke="var(--red)" stroke-width="2"/>
      <polygon class="blue-wedge" points="0,95 0,337 640,337" fill="var(--blue)"/>
    </svg>

    <div class="headline-block">
      <p class="kicker">Short stop or long stay</p>
      <h1 class="headline"><span class="mark-blue">Ticket must</span> be<br>validated<br>in the shop.</h1>
    </div>

    <div class="hours">
      <h2 class="hours-title">Shop <span class="mark-red">Opening</span><br>Hours.</h2>
      <p class="hours-list">Mon – Fri: 05:30 – 22:00<br>Sat &amp; Sun: 08:00 – 22:00</p>
    </div>

    <div class="notice">
      <h2 class="notice-title">Please <span class="mark-blue">review carefully</span></h2>
      <ul class="lang-list">
        <li class="lang-item">English (EN): Don't forget to validate your entry ticket in the shop – mandatory, even for short stops!</li>
        <li class="lang-item">French (FR): N'oubliez pas de valider votre ticket à la boutique – obligatoire, même pour un court arrêt !</li>
        <li class="lang-item">Dutch (NL): Vergeet je ticket niet te valideren in de shop – verplicht, ook bij kort parkeren!</li>
        <li class="lang-item">German (DE): Vergessen Sie nicht, Ihr Einfahrticket im Shop zu entwerten – Pflicht, auch bei kurzem Parken!</li>
        <li class="lang-item">Polish (PL): Nie zapomnij zatwierdzić biletu w sklepie – obowiązkowe, nawet przy krótkim postoju!</li>
        <li class="lang-item">Romanian (RO): Nu uitați să validați biletul în magazin – obligatoriu, chiar și pentru opriri scurte!</li>
      </ul>
    </div>

    <div class="brand"><span class="brand-square"></span>Haulport 41Ter</div>
  </section>
</body>
</html>
```